Website Design Request - Management Consulting Firm

We need a Website designed for an IT Management Staffing and Recruiting firm called TRAVENOK based in San Francisco.

The firm is an high-end technology staffing agency. Our focus is on quality and high-caliber candidates rather than quantity.

The website will have two main home pages. One for the recruiter and another on for the candidates.

The website needs to optimize for mobile devices as well.

I have attached few mock-ups that I have done just to show what I am thinking. The UI needs to be very clean, fluid, and it needs to have a modern, rustic, professional feel to it.

Target Market(s)

Technology Manager, Director, VP, CIO of Companies that have $4b-10b dollar revenue. Such as larkspurdwellings.example , https://www.velmorian.example/, quillnet.example, zib.example

Industry/Entity Type

Management Consulting

Number of Pages Required

5+ page

Font styles to use
Sans Serif

Colors
f37122
ffffff

Requirements
Must have
• Please review mock-ups for suggestions
Nice to have
Should not have

```html
<!DOCTYPE html>
<html lang="en">
<head>
<meta charset="utf-8">
<title>TRAVENOK — Project Management Consulting</title>
<link rel="stylesheet" href="https://fonts.googleapis.com/css2?family=Jost:wght@400;500;600&family=Arimo:wght@400;700&display=swap">
<style>
:root{
  --orange:#f37122;
  --white:#ffffff;
  --ink:#1f1f1f;
  --text:#4a4a4a;
  --muted:#7b7b7b;
  --line:#d9d9d9;
  --icon:#5f5f5f;
  --footer:#f2f2f2;
}
*{box-sizing:border-box;margin:0;padding:0}
html,body{width:1200px;height:2476px;overflow:hidden;background:var(--white)}
body{position:relative;font-family:"Jost",sans-serif;color:var(--ink)}
.abs{position:absolute}

/* header */
.site-header{position:absolute;left:0;top:0;width:1200px;height:104px;background:var(--white)}
.brand{position:absolute;display:flex;flex-direction:column;align-items:flex-start}
.brand-name{color:var(--orange);font-family:"Jost",sans-serif;font-weight:600;letter-spacing:1px;line-height:1}
.brand-tag{color:var(--ink);font-family:"Jost",sans-serif;font-weight:500;letter-spacing:.6px;text-transform:uppercase;line-height:1}
.site-header .brand{left:132px;top:20px}
.site-header .brand-name{font-size:44px}
.site-header .brand-tag{font-size:11.5px;margin-top:4px}
.nav-link{position:absolute;top:38px;font-size:15px;font-weight:500;color:var(--ink)}
.btn-outline,.btn-solid{position:absolute;top:31px;height:37px;display:flex;align-items:center;justify-content:center;gap:9px;font-size:15px}
.btn-outline{left:837px;width:102px;border:1.5px solid var(--orange);color:var(--orange)}
.btn-solid{left:965px;width:101px;background:var(--orange);color:var(--white)}

/* hero */
.hero{position:absolute;left:0;top:104px;width:1200px;height:553px;
  background:linear-gradient(180deg,#6b7078 0%,#8d9197 45%,#9fa2a6 100%)}
.hero-title{position:absolute;left:0;width:1200px;top:80px;text-align:center;color:var(--white);font-size:37px;font-weight:500;letter-spacing:.3px}
.hero-sub{position:absolute;left:0;width:1200px;top:136px;text-align:center;color:var(--white);font-family:"Arimo",sans-serif;font-size:20px}
.search-box{position:absolute;left:183px;top:231px;width:581px;height:66px;background:var(--white);border:3px solid #3a3a3a;outline:2px solid var(--white);display:flex;align-items:center;padding-left:28px;gap:18px;font-family:"Arimo",sans-serif;font-size:14px;color:var(--ink)}
.cta{position:absolute;left:776px;top:231px;width:240px;height:66px;background:var(--orange);color:var(--white);font-size:20px;font-weight:500;display:flex;align-items:center;justify-content:center;letter-spacing:.5px}
.terms{position:absolute;left:183px;top:318px;color:var(--white);font-family:"Arimo",sans-serif;font-size:15px}
.terms b{text-decoration:underline}
.resume-line{position:absolute;left:0;width:1200px;top:459px;display:flex;justify-content:center;align-items:center;gap:6px;color:var(--white);font-family:"Arimo",sans-serif;font-size:15px}
.resume-btn{background:var(--orange);padding:7px 8px}

/* tabs */
.tab{position:absolute;top:718px;width:249px;height:61px;border:1.5px solid #6a6a6a;display:flex;align-items:center;justify-content:center;gap:14px;font-size:19px;color:var(--ink)}
.tab.active{border-color:var(--orange);color:var(--orange);background:var(--white)}
.tab-caret{position:absolute;left:116px;bottom:-10px;width:18px;height:18px;background:var(--white);border-right:1.5px solid var(--orange);border-bottom:1.5px solid var(--orange);transform:rotate(45deg)}

.section-title{position:absolute;left:0;width:1200px;top:845px;text-align:center;color:var(--orange);font-size:29px;font-weight:500;letter-spacing:.5px}
.title-rule{position:absolute;left:512px;top:902px;width:145px;height:3px;background:var(--line)}

/* features */
.feature{position:absolute;width:300px;text-align:center}
.icon-ring{width:136px;height:136px;border-radius:50%;border:1.5px solid var(--line);margin:0 auto;display:flex;align-items:center;justify-content:center;background:var(--white)}
.feature h3{font-size:16px;font-weight:500;letter-spacing:.4px;margin-top:48px;color:var(--ink)}
.feature p{font-size:12.5px;line-height:21px;color:var(--muted);margin:14px auto 0;width:225px}
.values .feature h3{margin-top:52px;font-size:17px}
.values .feature p{width:330px;margin-left:-15px;margin-top:12px}
.divider{position:absolute;left:130px;top:1767px;width:939px;height:1.5px;background:var(--line)}

/* footer */
.site-footer{position:absolute;left:0;top:2181px;width:1200px;height:295px;background:var(--footer)}
.site-footer .brand{left:132px;top:56px}
.site-footer .brand-name{font-size:58px}
.site-footer .brand-tag{font-size:15px;margin-top:4px}
.foot-head{position:absolute;top:52px;color:var(--orange);font-size:14px;font-weight:500;letter-spacing:.5px}
.contact-list{position:absolute;left:558px;top:86px;list-style:none;font-size:12.5px;color:var(--text);line-height:21px}
.contact-list li{display:flex;gap:18px;margin-bottom:6px}
.contact-list svg{flex:none;margin-top:5px}
.social{position:absolute;top:93px;width:42px;height:42px;border-radius:50%;border:1.5px solid #2f3d8a;background:var(--white)}
.foot-rule{position:absolute;left:130px;top:207px;width:939px;height:1.5px;background:var(--line)}
.copyright{position:absolute;left:0;width:1200px;top:242px;text-align:center;font-size:11.5px;color:var(--text)}
</style>
</head>
<body>

<header class="site-header">
  <div class="brand"><span class="brand-name">TRAVENOK</span><span class="brand-tag">Project Management Consulting</span></div>
  <span class="nav-link" style="left:602px">Professionals</span>
  <span class="nav-link" style="left:731px">Employers</span>
  <a class="btn-outline"><svg width="12" height="14" viewBox="0 0 12 14"><rect x="1" y="6" width="10" height="8" fill="#f37122"/><path d="M3 6V4a3 3 0 0 1 6 0v2" fill="none" stroke="#f37122" stroke-width="1.8"/></svg>Sign In</a>
  <a class="btn-solid"><svg width="15" height="14" viewBox="0 0 15 14"><rect x="1" y="2" width="10" height="11" fill="none" stroke="#fff" stroke-width="1.6"/><path d="M6 9l1-3 6-6 2 2-6 6z" fill="#fff"/></svg>Sign Up</a>
</header>

<section class="hero" role="img" aria-label="Photo of smiling business professionals in a bright office meeting">
  <h1 class="hero-title">FILL IT PROJECT MANAGEMENT POSITIONS FAST</h1>
  <p class="hero-sub">Search our network and hire TOP IT PM Talents for permanent &amp; contract roles</p>
  <div class="search-box"><svg width="12" height="13" viewBox="0 0 12 13"><circle cx="6" cy="3.5" r="3" fill="#1f1f1f"/><path d="M0 13c0-4 2.5-6 6-6s6 2 6 6z" fill="#1f1f1f"/></svg>IT PROJECT MANAGER</div>
  <a class="cta">GET STARTED</a>
  <p class="terms">By entering your email address, you agree to our <b>Terms &amp; conditions</b></p>
  <p class="resume-line">Looking for a Job? <span class="resume-btn">Upload Resume</span> and let companies send you others</p>
</section>

<nav>
  <a class="tab" style="left:201px"><svg width="16" height="16" viewBox="0 0 16 16"><circle cx="6.5" cy="6.5" r="5" fill="none" stroke="#1f1f1f" stroke-width="2"/><path d="M10 10l5 5" stroke="#1f1f1f" stroke-width="2.4"/></svg>Our Focus</a>
  <a class="tab active" style="left:475px"><svg width="16" height="22" viewBox="0 0 16 22"><circle cx="8" cy="8" r="7" fill="#f37122"/><rect x="5" y="15" width="6" height="5" fill="#555"/></svg>Why us?<span class="tab-caret"></span></a>
  <a class="tab" style="left:749px"><svg width="16" height="16" viewBox="0 0 16 16"><circle cx="8" cy="8" r="5" fill="none" stroke="#1f1f1f" stroke-width="4" stroke-dasharray="2.6 1.3"/><circle cx="8" cy="8" r="2" fill="#fff"/></svg>How it Works?</a>
</nav>

<h2 class="section-title">WHY COMPANIES LOVE US</h2>
<div class="title-rule"></div>

<section class="benefits">
  <article class="feature" style="left:246px;top:950px">
    <div class="icon-ring"><svg width="64" height="64" viewBox="0 0 64 64"><circle cx="36" cy="26" r="18" fill="none" stroke="#5f5f5f" stroke-width="4"/><circle cx="36" cy="21" r="6" fill="#f37122"/><path d="M25 36c2-6 6-8 11-8s9 2 11 8z" fill="#f37122"/><path d="M22 40L8 54" stroke="#5f5f5f" stroke-width="6" stroke-linecap="round"/></svg></div>
    <h3>HIRE FAST</h3>
    <p>TRAVENOK is the fastest, most cost-effective way to fill your candidate pipeline.With just few clicks, employer can shortlistWith just few clicks, employer can shortlist</p>
  </article>
  <article class="feature" style="left:642px;top:950px">
    <div class="icon-ring"><svg width="66" height="66" viewBox="0 0 66 66"><circle cx="33" cy="33" r="30" fill="#5f5f5f" stroke="#5f5f5f" stroke-width="4" stroke-dasharray="5 3"/><circle cx="33" cy="33" r="20" fill="#f37122" stroke="#fff" stroke-width="3"/><path d="M23 33l7 7 13-14" fill="none" stroke="#fff" stroke-width="5"/></svg></div>
    <h3>HIRE THE BEST</h3>
    <p>We follow a strigent signup process toensure only the highest caliber professionals are accepted in our database.</p>
  </article>
  <article class="feature" style="left:246px;top:1381px">
    <div class="icon-ring"><svg width="66" height="66" viewBox="0 0 66 66"><path d="M33 18a13 13 0 0 0-8 23v7h16v-7a13 13 0 0 0-8-23z" fill="none" stroke="#5f5f5f" stroke-width="3"/><rect x="27" y="51" width="12" height="5" fill="#5f5f5f"/><g stroke="#f37122" stroke-width="3" stroke-linecap="round"><path d="M33 4v7M12 13l5 5M54 13l-5 5M4 31h7M62 31h-7M12 50l5-4M54 50l-5-4"/></g></svg></div>
    <h3>FIND NICHE SKILLS</h3>
    <p>Our propriety talent engine saves you time by finding the best matching cadidates for your niche project requirements.</p>
  </article>
  <article class="feature" style="left:642px;top:1381px">
    <div class="icon-ring"><svg width="74" height="52" viewBox="0 0 74 52"><path d="M4 14l12-6 6 18-10 5z" fill="#f37122"/><path d="M70 14l-12-6-6 18 10 5z" fill="#f37122"/><path d="M20 14l14-3 12 6 12-4 5 15-16 14-10-2-14-10z" fill="#5f5f5f"/><path d="M34 17l-6 6 6 2 6-5" fill="none" stroke="#fff" stroke-width="2"/></svg></div>
    <h3>MAKE BETTER HIRING</h3>
    <p>Candidates who have decided to join TRAVENOK are more engaged, maintain a high level of professionlaism and produce a higher ROI</p>
  </article>
</section>

<div class="divider"></div>

<section class="values">
  <article class="feature" style="left:111px;top:1841px">
    <div class="icon-ring"><svg width="74" height="60" viewBox="0 0 74 60"><path d="M70 4L4 30l24 6z" fill="#5f5f5f"/><path d="M70 4L28 36l6 20z" fill="#f37122"/><path d="M70 4L34 56l10-14 14 8z" fill="#5f5f5f"/></svg></div>
    <h3>OUR MISSION</h3>
    <p>To deliver the highest caliber Project Management Professionals for every project while eliminating the pain of hiring.</p>
  </article>
  <article class="feature" style="left:450px;top:1841px">
    <div class="icon-ring"><svg width="50" height="72" viewBox="0 0 50 72"><circle cx="25" cy="22" r="20" fill="#5f5f5f"/><circle cx="25" cy="22" r="13" fill="#fff"/><circle cx="25" cy="22" r="8" fill="#f37122"/><rect x="18" y="44" width="14" height="26" fill="#5f5f5f"/></svg></div>
    <h3>OUR VISION</h3>
    <p>Become the one-stop-shop for all IT PM needs. Resources, methodology and training.</p>
  </article>
  <article class="feature" style="left:789px;top:1841px">
    <div class="icon-ring"><svg width="80" height="80" viewBox="0 0 80 80"><path d="M38 18l7 14 15 2-11 11 3 15-14-7-14 7 3-15-11-11 15-2z" fill="none" stroke="#5f5f5f" stroke-width="3" stroke-linejoin="round"/><circle cx="64" cy="10" r="5" fill="none" stroke="#f37122" stroke-width="3"/><circle cx="10" cy="50" r="4" fill="none" stroke="#f37122" stroke-width="3"/><circle cx="66" cy="66" r="6" fill="none" stroke="#f37122" stroke-width="3"/></svg></div>
    <h3>CORE VALUES</h3>
    <p>Deliver the highest level of services at a reasonable profit while fostering a culture of innovation and growth.</p>
  </article>
</section>

<footer class="site-footer">
  <div class="brand"><span class="brand-name">TRAVENOK</span><span class="brand-tag">Project Management Consulting</span></div>
  <h4 class="foot-head" style="left:558px">CONTACT US</h4>
  <ul class="contact-list">
    <li><svg width="9" height="13" viewBox="0 0 9 13"><path d="M4.5 0a4.5 4.5 0 0 0-4.5 4.5C0 8 4.5 13 4.5 13S9 8 9 4.5A4.5 4.5 0 0 0 4.5 0z" fill="#1f1f1f"/><circle cx="4.5" cy="4.5" r="1.7" fill="#f2f2f2"/></svg><span>418 Orchard Bend Road, Marlow Springs,<br>CA 95010.</span></li>
    <li><svg width="12" height="9" viewBox="0 0 12 9"><rect width="12" height="9" fill="#1f1f1f"/><path d="M0 0l6 5 6-5" fill="none" stroke="#f2f2f2" stroke-width="1.2"/></svg><span>Email: office@travenoktech.example</span></li>
  </ul>
  <h4 class="foot-head" style="left:911px">FOLLOW US</h4>
  <a class="social" style="left:911px" aria-label="Social profile one"></a>
  <a class="social" style="left:966px;border-color:#5fb4e8" aria-label="Social profile two"></a>
  <a class="social" style="left:1023px" aria-label="Social profile three"></a>
  <div class="foot-rule"></div>
  <p class="copyright">Copyrihgts @ 2016 All Rights Reserved</p>
</footer>

</body>
</html>
```